Google Form Graphic to suit our Brand and industry

Create a graphic / image for us to put at the top of our client enquiry google form.
The image will be a section of an architectural home with our branding over the top. Preferably translucent.
The image must suit the shape of the google forms image, which is an elongated rectangle
#003d5d - brand colour

Target Market(s)

residential home owners, high end architectural homes

Industry/Entity Type

Residential construction

Colors
0054AA
0677BA
7BADD7
CADEEF
E8F1F8

Requirements
Must have
• our branding and a photo of an architectural home in the background

```html
<!DOCTYPE html>
<html lang="en">
<head>
<meta charset="UTF-8">
<title>Norva Build – Form Header Options</title>
<link rel="stylesheet" href="https://fonts.googleapis.com/css2?family=Poppins:wght@400;500&display=swap">
<style>
  :root {
    --brand-deep: #003d5d;
    --brand-blue: #0054AA;
    --brand-mid: #0677BA;
    --brand-light: #7BADD7;
    --brand-pale: #CADEEF;
    --brand-mist: #E8F1F8;
    --paper: #ffffff;
    --ink: #1a1a1a;
  }
  * { margin: 0; padding: 0; box-sizing: border-box; }
  html, body { width: 1200px; height: 1114px; overflow: hidden; background: var(--paper); }
  body { position: relative; font-family: "Poppins", sans-serif; }

  .option-label {
    position: absolute;
    left: 196px;
    font-size: 11px;
    font-weight: 400;
    letter-spacing: 0.32em;
    color: var(--ink);
  }
  .banner {
    position: absolute;
    left: 197px;
    width: 816px;
    height: 205px;
    overflow: hidden;
  }
  .banner-photo {
    position: absolute; inset: 0;
    background:
      linear-gradient(180deg, rgba(255,255,255,0) 55%, rgba(150,140,130,0.35) 100%),
      linear-gradient(90deg, #3c4650 0%, #5b6670 28%, #a9c6e2 42%, #cfe0ee 55%, #9fb4a0 62%, #d9d6d0 75%, #ece6dc 88%, #d8d2ca 100%);
  }
  .banner-overlay { position: absolute; inset: 0; width: 100%; height: 100%; }
  .wordmark {
    position: absolute;
    left: 0;
    top: 50%;
    transform: translateY(-50%);
    font-weight: 500;
    color: var(--paper);
    white-space: nowrap;
    line-height: 1;
  }

  .option-a .wordmark { left: 96px; font-size: 24px; letter-spacing: 0.45em; }
  .option-b .wordmark { left: 118px; font-size: 43px; letter-spacing: 0.3em; }
  .option-c .wordmark { left: 119px; font-size: 52px; letter-spacing: 0.3em; }
</style>
</head>
<body>

  <p class="option-label" style="top:86px;">OPTIONS A</p>
  <section class="banner option-a" style="left:195px; top:115px; width:818px; height:208px;">
    <div class="banner-photo" role="img" aria-label="Interior of an architectural home with a sweeping spiral staircase, glass balustrade and tall windows"></div>
    <svg class="banner-overlay" viewBox="0 0 818 208" preserveAspectRatio="none" aria-hidden="true">
      <defs>
        <linearGradient id="tint-a" x1="0" y1="0" x2="0" y2="1">
          <stop offset="0" stop-color="var(--brand-deep)" stop-opacity="0.9"/>
          <stop offset="1" stop-color="var(--brand-mid)" stop-opacity="0.88"/>
        </linearGradient>
      </defs>
      <polygon points="0,0 264,0 186,116 271,208 0,208" fill="url(#tint-a)"/>
    </svg>
    <p class="wordmark">NORVA BUILD</p>
  </section>

  <p class="option-label" style="top:440px;">OPTIONS B</p>
  <section class="banner option-b" style="top:467px;">
    <div class="banner-photo" role="img" aria-label="Interior of an architectural home with a sweeping spiral staircase, glass balustrade and tall windows"></div>
    <svg class="banner-overlay" viewBox="0 0 816 205" preserveAspectRatio="none" aria-hidden="true">
      <defs>
        <linearGradient id="tint-b" x1="0" y1="0" x2="0" y2="1">
          <stop offset="0" stop-color="var(--brand-deep)" stop-opacity="0.9"/>
          <stop offset="1" stop-color="var(--brand-mid)" stop-opacity="0.88"/>
        </linearGradient>
      </defs>
      <polygon points="0,0 343,0 272,77 354,205 0,205" fill="url(#tint-b)"/>
    </svg>
    <p class="wordmark">NORVA BUILD</p>
  </section>

  <p class="option-label" style="top:794px;">OPTIONS C</p>
  <section class="banner option-c" style="top:824px; height:204px;">
    <div class="banner-photo" role="img" aria-label="Interior of an architectural home with a sweeping spiral staircase, glass balustrade and tall windows"></div>
    <svg class="banner-overlay" viewBox="0 0 816 204" preserveAspectRatio="none" aria-hidden="true">
      <defs>
        <linearGradient id="tint-c" x1="0" y1="0" x2="0" y2="1">
          <stop offset="0" stop-color="var(--brand-deep)" stop-opacity="0.9"/>
          <stop offset="1" stop-color="var(--brand-mid)" stop-opacity="0.88"/>
        </linearGradient>
      </defs>
      <polygon points="0,0 377,0 316,53 381,204 0,204" fill="url(#tint-c)"/>
    </svg>
    <p class="wordmark">NORVA BUILD</p>
  </section>

</body>
</html>
```